Verdanith Website Concept

We would like a one page website. Please refer to the attached files for more information.

Please reference file attachment version 1.1.

```html
<!DOCTYPE html>
<html lang="en">
<head>
<meta charset="utf-8">
<title>Verdanith</title>
<link rel="stylesheet" href="https://fonts.googleapis.com/css2?family=Raleway:wght@300;400;500;700;800&family=Open+Sans:wght@400;600&family=Roboto:wght@500;700&display=swap">
<style>
:root{
  --navy:#3b4a7e;
  --navy-deep:#272c47;
  --navy-text:#34427a;
  --ink:#3a3a3a;
  --body:#555a62;
  --white:#ffffff;
  --line:#d8d8d8;
  --dark:#2b2b2b;
  --darker:#444444;
  --field-dark:#4a4a4a;
}
*{box-sizing:border-box;margin:0;padding:0}
html,body{width:1200px;height:3051px;overflow:hidden}
body{position:relative;background:var(--white);font-family:"Open Sans",Arial,sans-serif;color:var(--body)}
.abs{position:absolute}

/* header */
.site-header{position:absolute;top:0;left:0;width:1200px;height:98px;background:var(--white)}
.brand{position:absolute;left:100px;top:24px;display:flex;align-items:center;gap:14px}
.brand-mark{width:44px;height:44px;background:var(--navy)}
.brand-name{font-family:"Raleway",sans-serif;font-weight:500;font-size:32px;color:var(--navy-text);letter-spacing:1px}
.main-nav{position:absolute;top:40px;left:0;width:1200px;font-family:"Open Sans",sans-serif;font-size:15px;color:#555}
.main-nav span{position:absolute;white-space:nowrap}
.main-nav .is-active{color:var(--navy-text);font-weight:600}

/* hero */
.hero{position:absolute;top:98px;left:0;width:1200px;height:529px;
  background:radial-gradient(ellipse 260px 200px at 380px 240px,#e0a050 0%,rgba(200,120,40,.5) 35%,rgba(0,0,0,0) 70%),
  radial-gradient(ellipse 420px 260px at 300px 160px,#3b6a8a 0%,rgba(20,40,60,.4) 60%,rgba(0,0,0,0) 100%),
  linear-gradient(90deg,#101a24 0%,#1f2c36 45%,#1a2228 100%)}
.hero-caption{position:absolute;left:797px;top:205px;width:303px;color:var(--white);font-family:"Open Sans",sans-serif}
.hero-caption h1{font-weight:400;font-size:28px;letter-spacing:1px;padding-bottom:10px;border-bottom:1px solid rgba(255,255,255,.35)}
.hero-caption p{margin-top:12px;font-size:20px;line-height:31px;text-transform:uppercase}
.hero-arrow{position:absolute;top:340px;width:36px;height:36px;border-radius:50%;background:rgba(255,255,255,.12)}
.pager{position:absolute;left:0;width:1200px;display:flex;justify-content:center;gap:10px}
.pager i{width:6px;height:6px;border-radius:50%;background:#b5b5b5;display:block}
.pager i.on{background:var(--navy)}

/* who we are */
.section-title{position:absolute;left:0;width:1200px;text-align:center;font-family:"Raleway",sans-serif;font-size:38px;color:var(--navy-text);font-weight:300}
.section-title b{font-weight:800}
.about-text{position:absolute;left:100px;top:742px;width:1000px;text-align:center;font-size:13px;line-height:16px;color:#444}
.btn-read{position:absolute;left:510px;top:836px;width:200px;height:39px;background:var(--navy);color:var(--white);font-family:"Open Sans",sans-serif;font-size:14px;display:flex;align-items:center;justify-content:center;border-radius:2px}

/* services */
.services{position:absolute;top:913px;left:0;width:1200px;height:525px;
  background:radial-gradient(ellipse 300px 200px at 200px 280px,rgba(255,255,255,.9),rgba(255,255,255,0)),
  radial-gradient(ellipse 300px 220px at 950px 200px,rgba(255,255,255,.8),rgba(255,255,255,0)),
  linear-gradient(180deg,#dfe0e2 0%,#cfd1d4 50%,#e9e8e6 100%)}
.services-intro{position:absolute;left:0;top:66px;width:1200px;text-align:center;font-size:13px;color:#555}
.services-rule{position:absolute;left:100px;top:127px;width:1000px;height:1px;background:#bdbdbd}
.service{position:absolute;width:490px;display:flex;gap:22px}
.service-photo{width:134px;height:108px;flex:none}
.service h3{font-family:"Roboto",sans-serif;font-weight:700;font-size:16px;color:var(--ink);text-transform:uppercase;line-height:19px;margin-top:-2px}
.service p{margin-top:6px;font-size:13px;line-height:19px;color:#555}

/* testimonials */
.avatar{position:absolute;width:64px;height:64px;border-radius:50%;background:linear-gradient(135deg,#c9a08a,#7a4a3a)}
.quote-card{position:absolute;top:1556px;width:372px;height:132px;border:2px solid #e2e2e2;background:var(--white);padding:14px 24px}
.quote-card::before{content:"";position:absolute;left:-10px;top:18px;width:16px;height:16px;background:var(--white);border-left:2px solid #e2e2e2;border-bottom:2px solid #e2e2e2;transform:rotate(45deg)}
.quote-name{font-family:"Roboto",sans-serif;font-weight:500;font-size:15px;color:#222}
.quote-name small{font-size:10px;font-weight:400}
.quote-text{margin-top:8px;font-size:11px;line-height:22px;color:#999}

/* consultation */
.consult{position:absolute;top:1768px;left:0;width:1200px;height:728px;background:var(--navy)}
.consult .section-title{color:var(--white);top:34px;font-size:36px}
.consult-rule{position:absolute;left:497px;top:87px;width:225px;height:1px;background:rgba(255,255,255,.6)}
.consult-rule::after{content:"";position:absolute;left:60px;top:-2px;width:105px;height:5px;background:var(--white)}
.field-label{position:absolute;font-family:"Raleway",sans-serif;font-size:22px;color:var(--white)}
.field{position:absolute;width:262px;height:37px;background:var(--white)}
.field.select::after{content:"";position:absolute;right:0;top:0;width:42px;height:37px;background:var(--navy-deep)}
.select-caret{position:absolute;right:15px;top:15px;z-index:1}
.field.message{width:789px;height:112px;padding:12px 24px;font-size:13px;color:#777}
.btn-request{position:absolute;left:494px;top:642px;width:189px;height:45px;background:var(--navy-deep);color:var(--white);font-family:"Open Sans",sans-serif;font-size:18px;display:flex;align-items:center;justify-content:center}

/* contact */
.touch{position:absolute;top:2496px;left:0;width:1200px;height:488px;background:var(--dark)}
.touch .section-title{color:var(--white);top:52px;font-size:34px}
.social{position:absolute;top:140px;width:48px;height:48px;border:2px solid #666}
.social.on{border-color:var(--navy)}
.newsletter-note{position:absolute;left:0;top:222px;width:1200px;text-align:center;font-size:13px;color:#ddd}
.email-field{position:absolute;left:252px;top:270px;width:684px;height:53px;background:var(--field-dark);color:#ccc;font-size:13px;padding:17px 22px}
.btn-subscribe{position:absolute;left:519px;top:352px;width:150px;height:51px;border:2px solid #ddd;color:var(--white);font-weight:600;font-size:16px;display:flex;align-items:center;justify-content:center}
.to-top{position:absolute;left:1132px;top:418px}

.site-footer{position:absolute;top:2984px;left:0;width:1200px;height:67px;background:var(--darker);color:#ccc;font-size:14px;display:flex;align-items:center;justify-content:center}
</style>
</head>
<body>

<header class="site-header">
  <div class="brand"><span class="brand-mark"></span><span class="brand-name">Verdanith</span></div>
  <nav class="main-nav">
    <span class="is-active" style="left:545px">Home</span>
    <span style="left:639px">About Us</span>
    <span style="left:753px">Service</span>
    <span style="left:854px">Testimonials</span>
    <span style="left:993px">Contact</span>
    <span style="left:1064px">|</span>
    <svg class="abs" style="left:1087px;top:4px" width="16" height="16" viewBox="0 0 16 16"><circle cx="6.5" cy="6.5" r="5" fill="none" stroke="#555" stroke-width="1.6"/><line x1="10.2" y1="10.2" x2="14.5" y2="14.5" stroke="#555" stroke-width="1.8"/></svg>
  </nav>
</header>

<section class="hero" role="img" aria-label="Photo of a businessman touching a glowing dollar symbol surrounded by floating currency icons">
  <span class="hero-arrow" style="left:26px"></span>
  <span class="hero-arrow" style="left:1142px"></span>
  <svg class="abs" style="left:37px;top:351px" width="14" height="14" viewBox="0 0 14 14"><polyline points="9,2 4,7 9,12" fill="none" stroke="#888" stroke-width="2"/></svg>
  <svg class="abs" style="left:1153px;top:351px" width="14" height="14" viewBox="0 0 14 14"><polyline points="5,2 10,7 5,12" fill="none" stroke="#888" stroke-width="2"/></svg>
  <div class="hero-caption">
    <h1>VERDANITH</h1>
    <p>We are a financial security company.</p>
  </div>
</section>
<div class="pager" style="top:640px"><i class="on"></i><i></i><i></i></div>

<h2 class="section-title" style="top:686px"><b>VERDANITH</b> - WHO WE ARE</h2>
<p class="about-text">Verdanith is a United States-based tier one security firm specializing in the protection of financial services professionals, executives and their families. We manage engagements resulting from general and specific threats throughout the United States and abroad on behalf of our domestic clients. We deliver our services exclusively through associates and contractors with United States special operations, secret service, CIA, or equivalent experience and training. We are one of only a handful of domestic security firms that offers scalable, tier one security services in every market in the United States.</p>
<div class="btn-read">READ MORE</div>

<section class="services">
  <h2 class="section-title" style="top:20px;font-size:36px"><b>OUR SERVICES</b></h2>
  <p class="services-intro">Curabitur sagittis quam magna, ac facilisis lacus rutrum ut. Vivamus a lectus eu mauris cursus pharetra. Donec pulvinar mattis vestibulum.</p>
  <div class="services-rule"></div>

  <article class="service" style="left:100px;top:193px">
    <div class="service-photo" role="img" aria-label="Photo of a hand touching a digital security screen" style="background:linear-gradient(135deg,#5a3a30,#3a7ab0 50%,#2a2a30)"></div>
    <div><h3>Threat Assessment</h3><p>Etiam vel elit a ante varius sollicitudin. Cras at euismod nisi, at accumsan eros. Lorem ipsum dolor sit amet, consectetur adipiscing elit.</p></div>
  </article>
  <article class="service" style="left:616px;top:193px">
    <div class="service-photo" role="img" aria-label="Photo of a padlock on stacked binders" style="background:linear-gradient(135deg,#6a5a40,#c9a040 50%,#3a3020)"></div>
    <div><h3>Elite Executive Protection</h3><p>Nunc mi risus, bibendum ut lorem nec, porta condimentum tortor. Aliquam ac odio sagittis, fringilla turpis vel, sagittis dui. Cras id nibh nec nisl consectetur cursus.</p></div>
  </article>
  <article class="service" style="left:100px;top:350px">
    <div class="service-photo" role="img" aria-label="Photo of a padlock on stacked binders" style="background:linear-gradient(135deg,#7a6a50,#c9a040 50%,#4a3a20)"></div>
    <div><h3>Threat Avoidance Plan &amp; Dossier Creation</h3><p>Aenean porttitor, velit nec rutrum accumsan, est lectus pretium magna, quis malesuada nisi mauris ut ipsum. Curabitur sodales porttitor mollis.</p></div>
  </article>
  <article class="service" style="left:616px;top:350px">
    <div class="service-photo" role="img" aria-label="Photo of a businessman with an umbrella under stormy clouds" style="background:linear-gradient(180deg,#2a2a2a,#6a6a6a 60%,#3a3a3a)"></div>
    <div><h3>Threat Avoidance Plan &amp; Dossier Maintenance</h3><p>Maecenas posuere nisl sed tortor pulvinar, vitae suscipit ante eleifend. Nulla porta odio ut cursus molestie.</p></div>
  </article>
</section>

<h2 class="section-title" style="top:1468px;font-size:34px"><b>OUR CLIENT</b> TESTIMONIALS</h2>
<div class="avatar" role="img" aria-label="Client portrait" style="left:108px;top:1561px"></div>
<div class="quote-card" style="left:201px">
  <div class="quote-name">Jonas Pell / <small>lead partner, private firm</small></div>
  <p class="quote-text">" Vela is great, you should try it. The component is very easy to understand, the value is great too. And last but not least, vela is my favorite services."</p>
</div>
<div class="avatar" role="img" aria-label="Client portrait" style="left:639px;top:1561px;background:linear-gradient(135deg,#e8d0c0,#b08070)"></div>
<div class="quote-card" style="left:730px">
  <div class="quote-name">Jonas Pell / <small>lead partner, private firm</small></div>
  <p class="quote-text">" Vela is great, you should try it. The component is very easy to understand, the value is great too. And last but not least, vela is my favorite services."</p>
</div>
<div class="pager" style="top:1722px"><i class="on"></i><i></i><i></i></div>

<section class="consult">
  <h2 class="section-title"><b>REQUEST FOR</b> CONSULTATION</h2>
  <div class="consult-rule"></div>

  <label class="field-label" style="left:100px;top:140px">First Name:</label><div class="field" style="left:311px;top:136px"></div>
  <label class="field-label" style="left:628px;top:140px">Last Name:</label><div class="field" style="left:840px;top:136px"></div>
  <label class="field-label" style="left:100px;top:211px">Home Phone:</label><div class="field" style="left:311px;top:207px"></div>
  <label class="field-label" style="left:628px;top:211px">Work Phone:</label><div class="field" style="left:840px;top:207px"></div>
  <label class="field-label" style="left:100px;top:282px">Cell Phone:</label><div class="field" style="left:311px;top:278px"></div>
  <label class="field-label" style="left:628px;top:282px">Email Address:</label><div class="field" style="left:840px;top:278px"></div>
  <label class="field-label" style="left:100px;top:353px">Address:</label><div class="field" style="left:311px;top:349px"></div>
  <label class="field-label" style="left:628px;top:353px">City:</label><div class="field" style="left:840px;top:349px"></div>
  <label class="field-label" style="left:100px;top:424px">State:</label>
  <div class="field select" style="left:311px;top:420px"><svg class="select-caret" width="12" height="8" viewBox="0 0 12 8"><polygon points="0,0 12,0 6,8" fill="#fff"/></svg></div>
  <label class="field-label" style="left:628px;top:424px">Zip:</label><div class="field" style="left:840px;top:420px"></div>
  <label class="field-label" style="left:100px;top:490px">Message:</label>
  <div class="field message" style="left:311px;top:490px">Write your message Here</div>
  <div class="btn-request">REQUEST NOW</div>
</section>

<section class="touch">
  <h2 class="section-title"><b>GET IN</b> TOUCH</h2>
  <span class="social on" style="left:466px" aria-label="Social profile"></span>
  <span class="social" style="left:533px" aria-label="Social profile"></span>
  <span class="social" style="left:602px" aria-label="Social profile"></span>
  <span class="social" style="left:672px" aria-label="Social profile"></span>
  <p class="newsletter-note">Subscribe to our newsletter to stay update with what is new</p>
  <div class="email-field">Email Address</div>
  <div class="btn-subscribe">Subscribe</div>
  <svg class="to-top" width="36" height="22" viewBox="0 0 36 22"><polyline points="3,19 18,4 33,19" fill="none" stroke="#fff" stroke-width="4"/></svg>
</section>

<footer class="site-footer">verdanith.example © 2014 All Rights Reserved</footer>

</body>
</html>
```